Brightmill Data Works

Our company is about IT hardwares and IT solutions. IT hardware such as PC, RAMS, storage and servers. IT solutions such as project management, BA. We are also selling new technology too.

Target Market(s)

Consumer, Small to Medium Business, Corporate

Requirements
Must have
• The business card must have the following:
• Name:
• Title:
• Contact Number:
• Email address:
• Website:
• Color: Must match the logo color upgrade

```html
<!DOCTYPE html>
<html lang="en">
<head>
<meta charset="utf-8">
<title>Brightmill Data Works – Business Card</title>
<link href="https://fonts.googleapis.com/css2?family=Lato:wght@400;700;900&display=swap" rel="stylesheet">
<style>
  :root {
    --canvas: #2a2a2a;
    --card-black: #131313;
    --card-white: #f7f7f7;
    --ink-white: #ffffff;
    --ink-dark: #2b2b2b;
    --accent: #e08a24;
  }
  * { box-sizing: border-box; margin: 0; padding: 0; }
  html, body { width: 1200px; height: 900px; overflow: hidden; }
  body {
    background: var(--canvas);
    font-family: "Lato", sans-serif;
    position: relative;
  }
  .card {
    position: absolute;
    width: 525px;
    height: 300px;
    border-radius: 14px;
    overflow: hidden;
    background: var(--card-black);
  }
  .card--front { left: 90px; top: 110px; }
  .card--back { left: 585px; top: 490px; }

  /* Front */
  .brand-lockup {
    position: absolute;
    inset: 0;
    display: flex;
    flex-direction: column;
    align-items: center;
    justify-content: center;
    gap: 18px;
  }
  .brand-dot {
    width: 38px; height: 38px;
    border-radius: 50%;
    background: var(--accent);
  }
  .brand-name {
    color: var(--ink-white);
    font-weight: 900;
    font-size: 34px;
    letter-spacing: 1px;
    text-transform: uppercase;
  }

  /* Back */
  .contact {
    position: absolute;
    left: 34px; top: 0; bottom: 0;
    width: 330px;
    color: var(--ink-white);
  }
  .contact__name {
    position: absolute; top: 44px;
    font-size: 19px; font-weight: 400;
  }
  .contact__name b { font-weight: 700; }
  .contact__title {
    position: absolute; top: 68px; left: 16px;
    font-size: 11px; font-style: italic;
  }
  .contact__address {
    position: absolute; top: 134px;
    font-size: 12.5px; font-weight: 700;
  }
  .contact__list {
    position: absolute; top: 178px;
    list-style: none;
    display: flex; flex-direction: column; gap: 6px;
    font-size: 14px;
    line-height: 18px;
  }
  .contact__list li { display: flex; align-items: center; gap: 9px; }
  .contact__list svg { width: 15px; height: 13px; fill: var(--ink-white); flex: none; }

  .stripes {
    position: absolute; top: 0; bottom: 0; left: 372px;
    width: 22px;
    background: repeating-linear-gradient(90deg,
      var(--card-white) 0 3px, var(--card-black) 3px 6px);
  }
  .brand-panel {
    position: absolute; top: 0; bottom: 0; right: 0;
    width: 131px;
    background: var(--card-white);
  }
  .brand-panel__name {
    position: absolute;
    left: 50%; top: 50%;
    width: 260px;
    transform: translate(-50%, -50%) rotate(-90deg);
    text-align: center;
    color: var(--ink-dark);
    font-weight: 900;
    font-size: 26px;
    line-height: 1.15;
    letter-spacing: 1px;
    text-transform: uppercase;
  }
</style>
</head>
<body>

<section class="card card--front">
  <div class="brand-lockup">
    <span class="brand-dot"></span>
    <span class="brand-name">Brightmill Data Works</span>
  </div>
</section>

<section class="card card--back">
  <div class="contact">
    <p class="contact__name">Dana <b>Whitcombe</b></p>
    <p class="contact__title">Office Manager</p>
    <p class="contact__address">1180 Orchard Ln Fairview Ohio 45012</p>
    <ul class="contact__list">
      <li>
        <svg viewBox="0 0 16 14" aria-hidden="true"><path d="M1 4c0-2 3-3 7-3s7 1 7 3v1h-4V3.5H5V5H1zM3 6h10l2 7H1z"/></svg>
        555.014.2210
      </li>
      <li>
        <svg viewBox="0 0 16 14" aria-hidden="true"><path d="M4 0h8v4H4zM1 5h14v6h-3v3H4v-3H1zM5 9v4h6V9z"/></svg>
        555.014.2271
      </li>
      <li>
        <svg viewBox="0 0 16 14" aria-hidden="true"><path d="M0 1h16v12H0zM1.5 2.5v.3L8 8l6.5-5.2v-.3zM1.5 4.6v7h13v-7L8 9.8z"/></svg>
        dwhitcombe@brightmilldata.com
      </li>
      <li>
        <svg viewBox="0 0 16 14" aria-hidden="true"><path d="M8 0a7 7 0 1 0 0 14A7 7 0 0 0 8 0zm0 1.5c.7 0 1.6 1.6 1.9 4.7H6.1C6.4 3.1 7.3 1.5 8 1.5zM2.6 6.2a5.5 5.5 0 0 1 2.6-4C4.8 3.3 4.6 4.7 4.6 6.2zm8.8 0c0-1.5-.2-2.9-.6-4a5.5 5.5 0 0 1 2.6 4zM2.6 7.8h2c0 1.5.2 2.9.6 4a5.5 5.5 0 0 1-2.6-4zm3.5 0h3.8c-.3 3.1-1.2 4.7-1.9 4.7s-1.6-1.6-1.9-4.7zm5.3 0h2a5.5 5.5 0 0 1-2.6 4c.4-1.1.6-2.5.6-4z"/></svg>
        www.brightmilldata.com
      </li>
    </ul>
  </div>
  <div class="stripes"></div>
  <div class="brand-panel">
    <span class="brand-panel__name">Brightmill<br>Data Works</span>
  </div>
</section>

</body>
</html>
```